Recruitment of Trellan Staffing for the UK market

I want a website for the UK market to attract businesses and companies to come to us for Philipine labour. We want an information site that gives all information on what we do and how we can recruit Philippine labour.
This is a recruitment site for companies to contact us with their requirements for skilled workers coming from the Philipines over to the UK to work.

Target Market(s)

Uk Companies and businesses who want Philipine skilled workers

Industry/Entity Type

REcruitment

Coding

Number of Pages Required

5+ page

Font styles to use
Sans Serif

Colors
0054AA
0677BA
7BADD7
CADEEF
E8F1F8
0094D4
00A9DD
6FCCEA
C7EBF8
E9F6FB
EE7325
F08F49
F5BC92
FAE3D3
FDF4ED
EB3D1F
EC4F4E
F09395
F8D3D4
FCEDEE

Requirements
Must have
• Look professional and corperate with drop down menus for Home ,about, services,articles. training , contact us
Nice to have
• Look at Velmora recruitment- https://velmorarecruitment.example.co.uk/. This is my current site - https://www.trellanstaffing.example.com/
Should not have
• Cartoons or silly pictures , needs to be corperate looking

```html
<!DOCTYPE html>
<html lang="en">
<head>
<meta charset="utf-8">
<title>Trellan Staffing – Skilled Philippine Workers for UK Companies</title>
<link href="https://fonts.googleapis.com/css2?family=Outfit:wght@400;500;600&family=Mulish:wght@400;600;700;800&display=swap" rel="stylesheet">
<style>
:root{
  --brand:#0054AA;
  --brand-mid:#0677BA;
  --accent:#EE7325;
  --accent-light:#F08F49;
  --ink:#0f2f57;
  --text:#4a4f5c;
  --mist:#E8F1F8;
  --tint:#FAE3D3;
  --footer:#0b2d52;
  --white:#ffffff;
  --line:#CADEEF;
}
*{box-sizing:border-box;margin:0;padding:0}
html,body{width:1200px;height:4556px;overflow:hidden}
body{position:relative;background:var(--white);font-family:'Mulish',sans-serif;color:var(--text)}
.abs{position:absolute}
h1,h2,h3,.heading{font-family:'Outfit',sans-serif;color:var(--ink);font-weight:500}

/* Header */
.site-header{position:absolute;left:0;top:0;width:1200px;height:71px;background:var(--white);z-index:5}
.logo{position:absolute;display:flex;align-items:center;gap:8px;font-family:'Mulish',sans-serif;font-weight:800;font-size:20px;color:var(--brand)}
.logo .mark{width:14px;height:14px;background:currentColor}
.nav a{position:absolute;top:27px;font-size:12.5px;color:#444;text-decoration:none}
.nav a.active{color:var(--brand)}
.call{position:absolute;left:840px;top:19px;display:flex;align-items:center;gap:10px}
.call small{display:block;font-size:9px;color:#666;letter-spacing:.3px}
.call strong{display:block;font-size:17px;color:var(--brand);font-weight:800}
.header-cta{position:absolute;left:1023px;top:0;width:177px;height:71px;background:var(--brand);color:#fff;font-size:10.5px;font-weight:800;display:flex;align-items:center;justify-content:center;gap:8px;text-decoration:none}

/* Hero */
.hero{position:absolute;left:0;top:71px;width:1200px;height:680px;background:linear-gradient(100deg,#1c2530 0%,#2a3540 38%,#6c6a3a 62%,#b9b02a 78%,#3c4650 100%)}
.hero h1{position:absolute;left:97px;top:135px;font-size:39px;line-height:50px;color:#fff;font-weight:600}
.hero p{position:absolute;left:97px;top:302px;font-size:16px;line-height:25px;color:#fff}
.btn-outline{position:absolute;left:97px;top:381px;width:191px;height:44px;border:2px solid var(--accent-light);color:var(--accent-light);font-size:12.5px;font-weight:800;display:flex;align-items:center;justify-content:center}
.dots span{position:absolute;left:44px;width:7px;height:7px;border-radius:50%;background:#aab}
.dots span.on{left:40px;width:15px;height:15px;border:2px solid var(--accent-light);background:transparent}
.dots span.on::after{content:"";position:absolute;left:3px;top:3px;width:5px;height:5px;border-radius:50%;background:var(--accent-light)}

/* About */
.eyebrow-italic{font-style:italic;font-size:12.5px;color:var(--brand);font-weight:600}
.h-lg{font-size:38px;line-height:46px}
.body-copy{font-size:14.5px;line-height:26.5px;color:var(--text)}
.btn-accent{background:var(--accent);color:#fff;font-size:11px;font-weight:800;display:flex;align-items:center;justify-content:center}
.photo{position:absolute}

/* Working together */
.together{position:absolute;left:0;top:1343px;width:1200px;height:727px;background:var(--brand)}
.together h2{position:absolute;left:0;width:1200px;top:130px;text-align:center;color:#fff;font-size:35px}
.together h2 span{color:var(--accent-light)}
.together .intro{position:absolute;left:0;width:1200px;top:186px;text-align:center;color:#fff;font-size:14px;line-height:25px}
.card{position:absolute;top:268px;width:207px;height:319px;background:#fff}
.card .card-photo{position:absolute;left:0;top:0;width:207px;height:190px;clip-path:polygon(0 0,100% 0,100% 78%,0 100%)}
.card .hex{position:absolute;left:75px;top:107px}
.card h3{position:absolute;top:188px;left:0;width:207px;text-align:center;font-size:18px;font-weight:600;font-family:'Mulish',sans-serif;color:var(--ink)}
.card p{position:absolute;top:218px;left:18px;width:171px;text-align:center;font-size:11px;line-height:20px;color:#555}

/* Features */
.mist{position:absolute;left:0;top:2000px;width:1200px;height:1428px;background:var(--mist)}
.frame{position:absolute;border:3px solid var(--brand);border-radius:10px}
.eyebrow{font-family:'Mulish',sans-serif;font-size:13.5px;font-weight:700;color:var(--brand);letter-spacing:.2px;display:flex;align-items:center;gap:12px}
.eyebrow::before{content:"";width:20px;height:2px;background:var(--brand)}
.h-md{font-size:32px;line-height:40px;font-weight:500}
.feature-copy{font-size:13.5px;line-height:22.6px;color:var(--text)}
.learn{font-size:13px;font-weight:700;color:var(--accent);display:flex;align-items:center;gap:10px}
.connector{position:absolute;height:2px;background:var(--brand)}
.connector::after{content:"";position:absolute;top:-4px;width:10px;height:10px;border-radius:50%;background:var(--brand)}
.connector.to-right::after{right:-5px}
.connector.to-left::after{left:-5px}

/* Contact */
.contact-title{position:absolute;left:0;width:1200px;top:3490px;text-align:center;font-size:33px;font-weight:600}
.contact-sub{position:absolute;left:0;width:1200px;top:3543px;text-align:center;font-size:14px;color:#444}
.contact-h{font-family:'Mulish',sans-serif;font-size:27px;font-weight:600;color:var(--ink);letter-spacing:.3px}
.detail-label{font-size:15px;font-weight:800;color:var(--ink)}
.detail-value{font-size:13px;line-height:21px;color:#555}
.icon-badge{position:absolute;width:64px;height:64px}
.icon-badge::before{content:"";position:absolute;left:0;top:8px;width:56px;height:56px;border-radius:50%;background:var(--tint)}
.icon-badge svg{position:absolute;left:10px;top:0}
.form-card{position:absolute;left:601px;top:3628px;width:417px;height:507px;background:#fff;box-shadow:0 4px 24px rgba(20,30,50,.12);border-radius:4px;z-index:3}
.field{position:absolute;height:39px;border:1px solid var(--line);font-size:11px;color:#555;padding:12px 14px}
.send{position:absolute;left:26px;top:418px;width:364px;height:39px;background:var(--brand);color:#fff;font-size:12.5px;font-weight:800;display:flex;align-items:center;justify-content:center;gap:10px}

/* Footer */
.site-footer{position:absolute;left:0;top:4011px;width:1200px;height:545px;background:var(--footer);color:#fff}
.footer-h{position:absolute;font-size:14px;font-weight:800;color:#fff}
.footer-text{position:absolute;font-size:11.5px;line-height:19px;color:#e8ebf0}
.footer-links a{position:absolute;font-size:11.5px;color:#e8ebf0;text-decoration:none}
.social span{position:absolute;top:350px;width:28px;height:28px;border-radius:50%;border:1.5px solid #fff}
.social span.on{background:var(--accent);border-color:var(--accent)}
.newsletter{position:absolute;left:845px;top:309px;width:214px;height:35px;background:#fff;border-radius:18px;font-size:10.5px;color:#555;padding:11px 16px}
.newsletter i{position:absolute;right:2px;top:2px;width:31px;height:31px;border-radius:50%;background:var(--accent)}
.footer-rule{position:absolute;left:141px;top:477px;width:918px;height:1px;background:#2a4b70}
.legal{position:absolute;top:504px;font-size:11px;color:#e8ebf0}
</style>
</head>
<body>

<!-- Header -->
<header class="site-header">
  <div class="logo" style="left:80px;top:22px"><span class="mark"></span>Trellan Staffing</div>
  <nav class="nav">
    <a class="active" style="left:357px">Home</a>
    <a style="left:428px">About</a>
    <a style="left:499px">Services</a>
    <a style="left:583px">Articles</a>
    <a style="left:662px">Training</a>
    <a style="left:744px">Contact Us</a>
  </nav>
  <div class="call">
    <svg width="30" height="30" viewBox="0 0 30 30"><circle cx="15" cy="15" r="13.5" fill="none" stroke="#0054AA" stroke-width="2"/><path d="M10.5 9.5c1-.8 2-.6 2.5.3l1 2c.3.7 0 1.3-.6 1.7l-.7.5c.6 1.6 2 3 3.5 3.6l.5-.7c.4-.6 1-.9 1.7-.6l2 1c.9.5 1.1 1.5.3 2.5-1 1.2-2.7 1.6-4.2.8-3-1.5-5.5-4-7-7-.8-1.5-.3-3.2 1-4.1z" fill="#0054AA"/></svg>
    <div><small>CALL US TODAY</small><strong>07700900123</strong></div>
  </div>
  <a class="header-cta">GET STARTED NOW <svg width="14" height="10" viewBox="0 0 14 10"><path d="M0 5h12M8 1l4 4-4 4" stroke="#fff" stroke-width="1.5" fill="none"/></svg></a>
</header>

<!-- Hero -->
<section class="hero" role="img" aria-label="Photo of two engineers in hard hats and high-visibility jackets reviewing a laptop in a factory">
  <h1>Recruiting &amp; placing<br>Skilled Philippine workers<br>into UK companies.</h1>
  <p>We source skilled workers directly from the<br>Philippines to work in the UK.</p>
  <div class="btn-outline">GET STARTED NOW</div>
  <div class="dots">
    <span style="top:266px"></span>
    <span class="on" style="top:282px"></span>
    <span style="top:304px"></span>
    <span style="top:322px"></span>
  </div>
  <svg class="abs" style="left:96px;top:482px" width="12" height="18" viewBox="0 0 12 18"><path d="M6 0v16M1 11l5 5 5-5" stroke="#fff" stroke-width="1.5" fill="none"/></svg>
</section>
<svg class="abs" style="left:0;top:560px" width="1200" height="192" viewBox="0 0 1200 192"><path d="M0 182 C 180 195, 420 150, 640 120 C 880 90, 1080 110, 1200 60 L1200 192 L0 192 Z" fill="#fff"/></svg>

<!-- About -->
<section class="about">
  <div class="abs" style="left:0;top:867px;width:88px;height:2px;background:var(--brand)"></div>
  <div class="abs eyebrow-italic" style="left:106px;top:859px">About Trellan Staffing</div>
  <h2 class="abs h-lg" style="left:106px;top:883px">What the Business<br>is About</h2>
  <p class="abs body-copy" style="left:106px;top:992px;width:425px">We source skilled workers directly from the Philippines to work in the UK. With offices , training locations and specialist recruiters we can find the highest quality individuals to add value and resources to any UK buisness.</p>
  <p class="abs body-copy" style="left:106px;top:1125px;width:425px">We delivery quality based on vast experience over a number of years.</p>
  <div class="abs btn-accent" style="left:106px;top:1210px;width:138px;height:37px">LEARN MORE</div>
  <div class="photo" role="img" aria-label="Photo of a smiling site engineer in a blue hard hat shaking hands with a colleague" style="left:638px;top:756px;width:562px;height:498px;background:linear-gradient(120deg,#3b4a56 0%,#7d8a5c 35%,#b8c4cc 60%,#6f8fb0 100%)"></div>
  <div class="photo" role="img" aria-label="Photo of colleagues pointing at technical plans on a desk" style="left:562px;top:1078px;width:376px;height:336px;border:4px solid #fff;background:linear-gradient(140deg,#5a4a40 0%,#8b7060 40%,#cfc9c0 75%,#e6e3de 100%)"></div>
</section>

<!-- Working Together -->
<section class="together">
  <h2>Working <span>Together</span></h2>
  <p class="intro">We recruit the finest talent available with our dedicated 200 strong team.<br>Our centres are highlighted in red dots on the map.</p>

  <article class="card" style="left:140px">
    <div class="card-photo" role="img" aria-label="Photo of a smiling businesswoman in an office" style="background:linear-gradient(120deg,#d9d4cc,#6b7a82)"></div>
    <svg class="hex" width="56" height="62" viewBox="0 0 56 62"><polygon points="28,2 53,16 53,46 28,60 3,46 3,16" fill="#EE7325" stroke="#fff" stroke-width="3"/><circle cx="28" cy="26" r="6" fill="none" stroke="#fff" stroke-width="2"/><path d="M17 44c2-7 20-7 22 0" fill="none" stroke="#fff" stroke-width="2"/></svg>
    <h3>What We Do</h3>
    <p>Our company has been established in the Philippines for over 20 years. We have mainly been recruiting.</p>
  </article>

  <article class="card" style="left:380px">
    <div class="card-photo" role="img" aria-label="Photo of hands reviewing paperwork at a desk" style="background:linear-gradient(120deg,#eceae6,#8a8f96)"></div>
    <svg class="hex" width="56" height="62" viewBox="0 0 56 62"><polygon points="28,2 53,16 53,46 28,60 3,46 3,16" fill="#EE7325" stroke="#fff" stroke-width="3"/><rect x="18" y="18" width="20" height="26" fill="none" stroke="#fff" stroke-width="2"/><path d="M22 25h12M22 31h12M22 37h8" stroke="#fff" stroke-width="2"/></svg>
    <h3>How We Help</h3>
    <p>We work with companies to find skilled workers that meet the UK requirements for Visas and work permits.</p>
  </article>

  <article class="card" style="left:613px">
    <div class="card-photo" role="img" aria-label="Photo of two business people shaking hands" style="background:linear-gradient(120deg,#c9ccd0,#4d5560)"></div>
    <svg class="hex" width="56" height="62" viewBox="0 0 56 62"><polygon points="28,2 53,16 53,46 28,60 3,46 3,16" fill="#EE7325" stroke="#fff" stroke-width="3"/><circle cx="28" cy="24" r="5" fill="none" stroke="#fff" stroke-width="2"/><rect x="18" y="33" width="20" height="10" fill="none" stroke="#fff" stroke-width="2"/></svg>
    <h3>Where to Start</h3>
    <p>We need to know what your issues are and how we can understand the personnal you require , over what time.</p>
  </article>

  <article class="card" style="left:853px">
    <div class="card-photo" role="img" aria-label="Photo of a smiling woman in a yellow top with colleagues" style="background:linear-gradient(120deg,#6b6a66,#c9a640 60%,#8a8a80)"></div>
    <svg class="hex" width="56" height="62" viewBox="0 0 56 62"><polygon points="28,2 53,16 53,46 28,60 3,46 3,16" fill="#EE7325" stroke="#fff" stroke-width="3"/><path d="M19 22c1-1 2.5-1 3 .3l1.5 3c.3.7 0 1.3-.6 1.7l-1 .6c1 2.4 3 4.4 5.4 5.4l.6-1c.4-.6 1-.9 1.700-.6l3 1.5c1.3.5 1.3 2 .3 3-2 2-5 2-8 .2-3-2-5.5-4.5-7.3-7.5-1.8-3-1.5-5.5.4-6.6z" fill="none" stroke="#fff" stroke-width="2"/></svg>
    <h3>Contact Us Today</h3>
    <p>Please contact us today with your requirements , this can be care workers ,chef, welders, pipe fitters caravan.</p>
  </article>
</section>

<!-- Feature blocks -->
<section class="mist"></section>
<svg class="abs" style="left:0;top:1990px" width="1200" height="82" viewBox="0 0 1200 82"><path d="M0 0 L1200 0 L1200 78 C 1000 80, 820 40, 600 44 C 380 48, 200 20, 0 15 Z" fill="#0054AA"/></svg>

<div class="frame" style="left:88px;top:2205px;width:499px;height:269px;border-top-color:transparent;border-right-color:transparent"></div>
<div class="photo" role="img" aria-label="Photo of a presenter leading a business meeting with a whiteboard" style="left:101px;top:2165px;width:497px;height:300px;background:linear-gradient(120deg,#c8ccd0 0%,#8e969e 45%,#3f4650 100%)"></div>
<div class="connector to-right" style="left:598px;top:2211px;width:47px"></div>
<div class="abs eyebrow" style="left:682px;top:2174px">TRELLAN STAFFING</div>
<h2 class="abs h-md" style="left:682px;top:2196px">UK Skilled Workers List</h2>
<p class="abs feature-copy" style="left:682px;top:2253px;width:405px">The UK government since brexit have developed a new system based on points (similar to Australia) when recruiting from outside of the UK. Previuosly EU citizens could work in the UK without any extensive documentation or clarification of skills. This has all changed. Overseas recruitment must now focus on skills that are currently short in the UK. The list is extensive and is constandly being reviewed.</p>
<div class="abs learn" style="left:682px;top:2436px">Learn More <svg width="14" height="10" viewBox="0 0 14 10"><path d="M0 5h12M8 1l4 4-4 4" stroke="#EE7325" stroke-width="1.5" fill="none"/></svg></div>

<div class="abs eyebrow" style="left:88px;top:2634px">TRELLAN STAFFING</div>
<h2 class="abs h-md" style="left:88px;top:2657px">Sponsor Licence</h2>
<p class="abs feature-copy" style="left:88px;top:2714px;width:405px">If you have areas of your business that meet the entry requirements of skilled labour your next step is to gain a sponsor licence for your business. There are different types of licences depending on the size of the business.</p>
<p class="abs feature-copy" style="left:88px;top:2827px">All information can be found here-</p>
<div class="abs learn" style="left:88px;top:2883px">Learn More <svg width="14" height="10" viewBox="0 0 14 10"><path d="M0 5h12M8 1l4 4-4 4" stroke="#EE7325" stroke-width="1.5" fill="none"/></svg></div>
<div class="frame" style="left:612px;top:2633px;width:498px;height:270px;border-top-color:transparent;border-left-color:transparent"></div>
<div class="photo" role="img" aria-label="Photo of a woman in a car taking notes on a clipboard" style="left:601px;top:2596px;width:497px;height:299px;background:linear-gradient(120deg,#1f262e 0%,#4a525c 40%,#c9c3b0 70%,#e8c14a 85%,#2a3038 100%)"></div>
<div class="connector to-left" style="left:553px;top:2667px;width:48px"></div>

<div class="frame" style="left:88px;top:3062px;width:499px;height:269px;border-top-color:transparent;border-right-color:transparent"></div>
<div class="photo" role="img" aria-label="Photo of a smiling businesswoman shaking hands across a table" style="left:101px;top:3022px;width:497px;height:300px;background:linear-gradient(120deg,#8a8f94 0%,#3a3f46 45%,#2c6b70 80%,#1f4a50 100%)"></div>
<div class="connector to-right" style="left:598px;top:3070px;width:47px"></div>
<div class="abs eyebrow" style="left:682px;top:3031px">TRELLAN STAFFING</div>
<h2 class="abs h-md" style="left:682px;top:3055px">Recruitment Timeline</h2>
<p class="abs feature-copy" style="left:682px;top:3111px;width:405px">Brief us on the job profiles – this is passed on to our teams in the Philippines. Our teams in the Philippines source suitable candidates, documentation required for each candidate will be checked and vetted by the Recruitment Team.</p>
<p class="abs feature-copy" style="left:682px;top:3224px;width:405px">Once deemed qualified, they will now be assessed by their Technical Interviewer .</p>
<div class="abs learn" style="left:682px;top:3293px">Learn More <svg width="14" height="10" viewBox="0 0 14 10"><path d="M0 5h12M8 1l4 4-4 4" stroke="#EE7325" stroke-width="1.5" fill="none"/></svg></div>

<!-- Contact -->
<h2 class="contact-title">Contact Us</h2>
<p class="contact-sub">Lorem ipsum dolor sit amet, consectetur adipisicing elit sed do eiusmod.</p>

<div class="abs contact-h" style="left:184px;top:3636px">CONTACT DETAILS</div>
<p class="abs detail-value" style="left:184px;top:3696px;width:290px">We source skilled workers directly from the Philippines to work in the UK.</p>

<div class="icon-badge" style="left:164px;top:3770px"><svg width="48" height="48" viewBox="0 0 48 48"><rect x="8" y="6" width="26" height="36" fill="none" stroke="#333" stroke-width="2"/><path d="M13 12h4M21 12h4M13 19h4M21 19h4M13 26h4M21 26h4M18 42v-8h6v8" stroke="#333" stroke-width="2"/><circle cx="37" cy="34" r="5" fill="#fff" stroke="#333" stroke-width="2"/></svg></div>
<div class="abs detail-label" style="left:260px;top:3772px">HEAD OFFICE</div>
<div class="abs detail-value" style="left:260px;top:3794px">Orchard Row, Kelmby<br>KB4 2 United Kingdom</div>

<div class="icon-badge" style="left:164px;top:3876px"><svg width="48" height="48" viewBox="0 0 48 48"><path d="M6 20 L24 6 L42 20 V42 H6 Z" fill="none" stroke="#333" stroke-width="2"/><path d="M6 20 L24 32 L42 20" fill="none" stroke="#333" stroke-width="2"/><circle cx="24" cy="19" r="5" fill="none" stroke="#333" stroke-width="2"/></svg></div>
<div class="abs detail-label" style="left:260px;top:3878px">EMAIL ADDRESS</div>
<div class="abs detail-value" style="left:260px;top:3901px">sales@trellanstaffing.example.com</div>

<div class="icon-badge" style="left:164px;top:3965px"><svg width="48" height="48" viewBox="0 0 48 48"><rect x="8" y="8" width="10" height="32" rx="3" fill="none" stroke="#333" stroke-width="2"/><rect x="18" y="12" width="22" height="28" fill="none" stroke="#333" stroke-width="2"/><path d="M22 18h14M23 25h3M29 25h3M23 31h3M29 31h3" stroke="#333" stroke-width="2"/></svg></div>
<div class="abs detail-label" style="left:260px;top:3971px">PHONE NUMBER</div>
<div class="abs" style="left:260px;top:3991px;font-size:20px;color:#333">07700900123</div>

<form class="form-card">
  <div class="abs contact-h" style="left:26px;top:40px">CONTACT US TODAY</div>
  <div class="field" style="left:26px;top:97px;width:177px">First Name*</div>
  <div class="field" style="left:214px;top:97px;width:176px">Last Name*</div>
  <div class="field" style="left:26px;top:148px;width:364px">Phone Number*</div>
  <div class="field" style="left:26px;top:198px;width:364px">Email Address*</div>
  <div class="field" style="left:26px;top:249px;width:364px">Location*<svg class="abs" style="right:14px;top:16px" width="10" height="6" viewBox="0 0 10 6"><path d="M0 0h10L5 6z" fill="#555"/></svg></div>
  <div class="field" style="left:26px;top:302px;width:364px;height:102px">Type your Message*</div>
  <div class="send">SEND MESSAGE <svg width="16" height="14" viewBox="0 0 16 14"><path d="M0 6 L16 0 L11 14 L8 8 Z" fill="#fff"/></svg></div>
</form>

<!-- Footer -->
<footer class="site-footer">
  <div class="logo" style="left:141px;top:176px;color:#7BADD7"><span class="mark"></span>Trellan Staffing</div>
  <p class="footer-text" style="left:141px;top:228px;width:250px">We source skilled workers directly from the Philippines to work in the UK. With offices , training locations and specialist...</p>
  <div class="social">
    <span style="left:139px"></span>
    <span class="on" style="left:174px"></span>
    <span style="left:209px"></span>
    <span style="left:244px"></span>
  </div>

  <div class="footer-h" style="left:459px;top:210px">Quick Links</div>
  <div class="footer-links">
    <a style="left:459px;top:250px">Home</a>
    <a style="left:459px;top:277px">About</a>
    <a style="left:459px;top:303px">Services</a>
    <a style="left:459px;top:330px">Articles</a>
    <a style="left:459px;top:356px">Training</a>
    <a style="left:459px;top:383px">Contact Us</a>
  </div>

  <div class="footer-h" style="left:606px;top:210px">Contact Details</div>
  <svg class="abs" style="left:605px;top:252px" width="10" height="14" viewBox="0 0 10 14"><path d="M5 0a5 5 0 0 1 5 5c0 4-5 9-5 9S0 9 0 5a5 5 0 0 1 5-5z" fill="#EE7325"/><circle cx="5" cy="5" r="2" fill="#0b2d52"/></svg>
  <p class="footer-text" style="left:624px;top:250px">Orchard Row,<br>Kelmby KB4 2<br>United Kingdom</p>
  <svg class="abs" style="left:605px;top:321px" width="12" height="12" viewBox="0 0 12 12"><path d="M2 1c.6-.5 1.3-.4 1.6.2l.8 1.5c.2.5 0 1-.4 1.2l-.5.4c.5 1.2 1.5 2.2 2.7 2.7l.4-.5c.3-.4.8-.6 1.2-.4l1.5.8c.6.3.7 1 .2 1.6-.8.9-2 1.1-3 .5C4.5 8 3 6.5 1.9 4.5 1.3 3.4 1.3 1.8 2 1z" fill="#EE7325"/></svg>
  <p class="footer-text" style="left:624px;top:318px">07700900123</p>
  <svg class="abs" style="left:605px;top:354px" width="12" height="9" viewBox="0 0 12 9"><rect width="12" height="9" fill="#EE7325"/><path d="M0 0l6 5 6-5" stroke="#0b2d52" fill="none"/></svg>
  <p class="footer-text" style="left:624px;top:349px">sales@trellanstaffing.example.com</p>

  <div class="footer-h" style="left:845px;top:210px">Our Newsletter</div>
  <p class="footer-text" style="left:845px;top:250px;width:230px">Lorem ipsum dolor sit amet, consectetur adipisicing elit, sed do eiusmod.</p>
  <div class="newsletter">Email Address...<i><svg class="abs" style="left:9px;top:9px" width="14" height="12" viewBox="0 0 16 14"><path d="M0 6 L16 0 L11 14 L8 8 Z" fill="#fff"/></svg></i></div>

  <div class="footer-rule"></div>
  <div class="legal" style="left:141px">Copyrights © 2023 All Rights Reserved | Trellan Staffing Ltd</div>
  <div class="legal" style="left:899px">Privacy Policy &nbsp;&nbsp; | &nbsp;&nbsp; Terms of Use</div>
</footer>
<svg class="abs" style="left:0;top:4010px;z-index:1" width="1200" height="56" viewBox="0 0 1200 56"><path d="M0 0 H1200 V2 C 950 20, 500 50, 0 55 Z" fill="#fff"/></svg>

</body>
</html>
```